Business Card Design Project

We are a construction company in Orange County, CA. We need a two sided business card. We would like the back to be our logo with web URL. Front should included Name, title, address, phone, fax and email address.

our address is
627 West Dorrance Blvd, Suite 308
Anaheim, CA 92718

Our logo files are attached.

Construction

```html
<!DOCTYPE html>
<html lang="en">
<head>
<meta charset="utf-8">
<title>Renvale Business Card</title>
<link rel="stylesheet" href="https://fonts.googleapis.com/css2?family=Arimo:wght@400;700&display=swap">
<style>
  :root {
    --brand-blue: #1d5290;
    --band-blue: #1f5593;
    --band-blue-dark: #173f70;
    --card-white: #ffffff;
    --divider: #c9d3df;
    --backdrop: #e6e8eb;
    --shadow: rgba(20, 30, 45, 0.22);
  }
  * { box-sizing: border-box; margin: 0; padding: 0; }
  html, body {
    width: 1200px; height: 900px; overflow: hidden;
    background: var(--backdrop);
    font-family: "Arimo", Arial, sans-serif;
  }
  .canvas {
    width: 1200px; height: 900px;
    display: flex; flex-direction: column;
    align-items: center; justify-content: center; gap: 48px;
  }
  .card {
    position: relative; width: 660px; height: 377px;
    border-radius: 24px; overflow: hidden;
    background: var(--card-white);
    box-shadow: 0 10px 28px var(--shadow);
  }

  /* Back side */
  .back-identity {
    position: absolute; left: 0; right: 0; top: 0; height: 270px;
    display: flex; flex-direction: column; align-items: center; justify-content: center;
  }
  .back-wordmark {
    font-weight: 700; font-size: 104px; letter-spacing: -2px;
    color: var(--brand-blue); line-height: 1;
  }
  .back-url {
    margin-top: 8px; font-size: 19px; color: var(--brand-blue);
    align-self: flex-end; margin-right: 100px;
  }
  .tagline-band {
    position: absolute; left: 0; right: 0; bottom: 0; height: 107px;
    background: var(--band-blue);
    display: flex; align-items: center; justify-content: center;
    color: var(--card-white); font-size: 26px; letter-spacing: 6px;
  }

  /* Front side */
  .front-header {
    position: absolute; left: 0; right: 0; top: 0; height: 146px;
    padding: 26px 0 0 52px;
  }
  .front-wordmark {
    font-weight: 700; font-size: 74px; letter-spacing: -1px;
    color: var(--brand-blue); line-height: 1;
  }
  .front-tagline {
    margin-top: 4px; font-size: 13px; font-weight: 700;
    letter-spacing: 4.2px; color: var(--brand-blue);
  }
  .front-rule {
    position: absolute; left: 0; right: 0; top: 146px; height: 10px;
    background: linear-gradient(to bottom, #e4e8ed, #b9c2cc);
  }
  .front-band {
    position: absolute; left: 0; right: 0; top: 156px; bottom: 0;
    background: linear-gradient(to bottom, var(--band-blue), var(--band-blue-dark));
    color: var(--card-white);
  }
  .contact-block { position: absolute; left: 44px; top: 20px; }
  .address { font-size: 19px; line-height: 23px; margin-bottom: 12px; }
  .contact-list { list-style: none; }
  .contact-item {
    display: flex; align-items: center; height: 28px; font-size: 21px;
  }
  .contact-icon { width: 18px; height: 18px; margin-right: 28px; flex: none; }
  .band-divider {
    position: absolute; left: 400px; top: 32px; bottom: 32px; width: 1px;
    background: var(--divider); opacity: 0.7;
  }
  .person { position: absolute; left: 436px; top: 84px; }
  .person-name { font-size: 27px; font-weight: 700; }
  .person-title { font-size: 19px; margin-top: 4px; }
</style>
</head>
<body>
<main class="canvas">

  <section class="card card-back" aria-label="Business card back">
    <div class="back-identity">
      <div class="back-wordmark">RENVALE</div>
      <div class="back-url">www.renvalebuild.com</div>
    </div>
    <div class="tagline-band">PLAN • DEVELOP • CONSTRUCT</div>
  </section>

  <section class="card card-front" aria-label="Business card front">
    <header class="front-header">
      <div class="front-wordmark">RENVALE</div>
      <div class="front-tagline">PLAN • DEVELOP • CONSTRUCT</div>
    </header>
    <div class="front-rule"></div>
    <div class="front-band">
      <div class="contact-block">
        <p class="address">627 West Dorrance Blvd, Suite 308<br>Anaheim, CA 92718</p>
        <ul class="contact-list">
          <li class="contact-item">
            <svg class="contact-icon" viewBox="0 0 20 20" aria-hidden="true"><path d="M2 7c0-3 4-4 8-4s8 1 8 4v2h-4V7H6v2H2z M5 10h10l2 7H3z" fill="#fff"/><circle cx="10" cy="13.5" r="1.8" fill="#1f5593"/></svg>
            (00) 555-0142-310
          </li>
          <li class="contact-item">
            <svg class="contact-icon" viewBox="0 0 20 20" aria-hidden="true"><rect x="3" y="2" width="14" height="16" rx="1.5" fill="#fff"/><rect x="6" y="4.5" width="8" height="4" fill="#1f5593"/><rect x="6" y="11" width="8" height="1.5" fill="#1f5593"/><rect x="6" y="14" width="8" height="1.5" fill="#1f5593"/></svg>
            (00) 555-0142-310
          </li>
          <li class="contact-item">
            <svg class="contact-icon" viewBox="0 0 20 20" aria-hidden="true"><rect x="2" y="5" width="16" height="11" fill="#fff"/><path d="M2 5l8 6 8-6" fill="none" stroke="#1f5593" stroke-width="1.5"/></svg>
            info@renvalebuild.com
          </li>
          <li class="contact-item">
            <svg class="contact-icon" viewBox="0 0 20 20" aria-hidden="true"><circle cx="10" cy="10" r="8" fill="#fff"/><g fill="none" stroke="#1f5593" stroke-width="1.1"><ellipse cx="10" cy="10" rx="3.5" ry="8"/><path d="M2 10h16M3.5 6h13M3.5 14h13"/></g></svg>
            www.renvalebuild.com
          </li>
        </ul>
      </div>
      <div class="band-divider"></div>
      <div class="person">
        <div class="person-name">Marcus Delaney</div>
        <div class="person-title">General Manager</div>
      </div>
    </div>
  </section>

</main>
</body>
</html>
```